www.marvenholt.com

Updating website so looks futristic but yet business like and easy to navigate, essentially a good landing page with a cool picture summing up what we do, and links to the following pages, all other pages on site to be updated, Exclusive Distributor of Brisk Forge Unique Fitness Equipment Products in UK & Ireland, www.crestvolley.co.uk Exclusive Partners & Distributors Of Crest Volley - Obstacle Races - Obstacle Hire - Obstacle Training - Adventure Events, www.goplumwick.co.uk Adventures That Inspire. We also Health Club / Facillity Consultancy

```html
<!DOCTYPE html>
<html lang="en">
<head>
<meta charset="utf-8">
<title>Marvenholt Leisure</title>
<link href="https://fonts.googleapis.com/css2?family=Roboto+Slab:wght@400;700&family=Open+Sans:wght@400;600;700&display=swap" rel="stylesheet">
<style>
:root{
  --yellow:#e3c200;
  --ink:#111;
  --text:#444;
  --muted:#888;
  --line:#ddd;
  --dark:#1d1d1d;
  --darker:#0c0c0c;
  --white:#fff;
  --club-sub:#5e5000;
}
*{box-sizing:border-box;margin:0;padding:0}
html,body{width:1200px;height:2731px;overflow:hidden;background:var(--white)}
body{position:relative;font-family:"Open Sans",Arial,sans-serif;color:var(--text)}
.abs{position:absolute}

/* header */
.topline{left:0;top:0;width:1200px;height:5px;background:var(--yellow)}
.header{left:0;top:5px;width:1200px;height:90px;background:var(--white);border-bottom:1px solid #e5e5e5}
.brand{left:82px;top:10px;font-family:"Roboto Slab",Georgia,serif;font-size:33px;color:var(--ink);letter-spacing:1px;text-transform:uppercase;white-space:nowrap}
.tagline{left:82px;top:58px;font-family:"Roboto Slab",Georgia,serif;font-size:14px;color:#aaa;word-spacing:4px}
.callus{left:734px;top:8px;font-size:14px;color:#888;white-space:nowrap}
.callus b{font-size:22px;color:var(--ink);font-weight:600;margin-left:4px}
.account{left:960px;top:0;width:167px;height:40px;background:#1e2226;color:#fff;font-size:15px;display:flex;align-items:center;justify-content:center;gap:10px;border-radius:0 0 3px 3px}
.nav{top:58px;font-size:14px;color:#333;text-transform:uppercase;white-space:nowrap}
.nav.active{color:var(--yellow)}
.nav.active::after{content:"";position:absolute;left:50%;top:29px;margin-left:-7px;border:7px solid transparent;border-bottom-color:#222}

/* hero */
.hero{left:0;top:95px;width:1200px;height:575px;background:radial-gradient(ellipse at 72% 45%,#5b5f64 0%,#2f3236 40%,#141517 100%)}
.hero-figures{left:530px;top:150px;width:520px;height:520px;background:radial-gradient(ellipse at 50% 45%,rgba(180,140,115,.55),rgba(60,60,70,0) 68%)}
.hero-kicker{left:78px;top:270px;font-size:23px;color:var(--yellow);font-family:"Roboto Slab",Georgia,serif}
.hero-title{left:78px;top:292px;font-size:64px;font-weight:700;color:#fff;letter-spacing:-1px;white-space:nowrap}
.hero-text{left:78px;top:380px;width:520px;font-size:18px;line-height:26px;color:#d0d0d0}
.btn-light{left:78px;top:450px;width:208px;height:56px;background:#fff;color:#222;font-size:18px;border-radius:3px;display:flex;align-items:center;justify-content:center;text-transform:uppercase}

/* welcome */
.section-title{left:0;width:1200px;text-align:center;font-family:"Roboto Slab",Georgia,serif;font-size:40px;color:var(--ink)}
.section-title span{color:var(--yellow)}
.welcome-text{left:127px;top:796px;width:956px;text-align:center;font-size:13px;line-height:22.5px;color:#555}
.card{top:985px;height:210px;width:334px}
.card-label{position:absolute;left:0;bottom:10px;width:100%;text-align:center;color:#fff;font-size:22px;font-family:"Roboto Slab",Georgia,serif}
.card-health{left:78px;background:linear-gradient(160deg,#b9d2a3,#e8e2c8 45%,#9fbf7a)}
.card-wellness{left:433px;background:linear-gradient(180deg,#e9e6dd 0%,#cfc6b4 55%,#6f8d9c 70%,#8a7a5c 100%)}
.card-fitness{left:789px;background:linear-gradient(150deg,#3a3a3a,#1a1a1a)}
.fitness-frame{position:absolute;left:12px;top:12px;right:12px;bottom:12px;border:1px solid #bbb;text-align:center;color:#fff;padding:18px 18px 0}
.fitness-frame h3{font-family:"Roboto Slab",Georgia,serif;font-weight:400;font-size:22px;margin-bottom:10px}
.fitness-frame p{font-size:13px;line-height:21px;color:#eee}

/* testimonial */
.testimonial-band{left:0;top:1256px;width:1200px;height:412px;background:radial-gradient(ellipse at 50% 45%,#fafafa 0%,#e6e6e6 60%,#d8d8d8 100%)}
.quote{left:118px;top:1374px;width:964px;text-align:center;font-size:13.5px;line-height:23px;color:#333}
.quote-rule{left:599px;top:1508px;width:1px;height:44px;background:#777}
.quote-name{left:0;top:1566px;width:1200px;text-align:center;font-family:"Roboto Slab",Georgia,serif;font-weight:700;font-size:20px;color:var(--ink)}
.quote-role{left:0;top:1604px;width:1200px;text-align:center;font-size:13.5px;color:#333}

/* team */
.member{top:1786px;width:234px}
.photo{width:234px;height:210px;background:linear-gradient(160deg,#2c3b5c 0%,#4c5f84 45%,#b49884 55%,#1f2738 100%);border:1px solid #222}
.photo.highlight{background:linear-gradient(160deg,#cdb21a,#d9bd1c 60%,#b79e12);display:flex;align-items:center;justify-content:center}
.link-box{width:52px;height:52px;border:2px solid rgba(255,255,255,.8);display:flex;align-items:center;justify-content:center}
.member-name{margin-top:16px;text-align:center;font-family:"Roboto Slab",Georgia,serif;font-size:22px;color:var(--yellow);white-space:nowrap}
.member-name.dark{color:var(--ink)}
.member-role{text-align:center;font-size:13px;color:#333;margin-top:2px}
.member-rule{margin-top:16px;height:2px;background:#e2e2e2}
.socials{display:flex;justify-content:center;gap:22px;margin-top:16px;align-items:center}
.dot{width:14px;height:14px;border-radius:50%;background:#999}
.arrow{top:1940px}

/* health club */
.club{left:78px;top:2231px;width:1044px;height:145px;background:var(--yellow)}
.club-figures{left:74px;top:2128px;width:186px;height:248px;background:linear-gradient(180deg,#8a8a8a 0%,#3b3b3b 40%,#1e1e1e 100%);border-radius:70px 70px 0 0}
.club-title{left:275px;top:2266px;font-family:"Roboto Slab",Georgia,serif;font-size:32px;color:#111;white-space:nowrap}
.club-sub{left:275px;top:2313px;font-size:15px;color:var(--club-sub);white-space:nowrap}
.btn-dark{left:874px;top:2278px;width:208px;height:51px;background:#0d0d0d;color:#fff;font-size:16px;font-weight:600;border-radius:3px;display:flex;align-items:center;justify-content:center;text-transform:uppercase}

/* footer */
.footer{left:0;top:2376px;width:1200px;height:305px;background:var(--dark)}
.foot-head{top:2418px;font-family:"Roboto Slab",Georgia,serif;font-size:22px;color:#fff}
.blog{left:78px;display:flex;gap:10px}
.avatar{width:54px;height:54px;border-radius:50%;border:2px solid #fff;background:linear-gradient(160deg,#d8a36a,#8aa9b8)}
.blog-title{font-size:14px;color:#fff;line-height:20px;width:180px}
.blog-meta{font-size:11px;color:#999;margin-top:4px}
.contact-item{left:350px;display:flex;gap:14px;align-items:flex-start}
.contact-item .label{font-size:15px;color:#aaa;line-height:18px}
.contact-item .value{font-size:14px;color:#fff;line-height:20px}
.field{border:1px solid #555;border-radius:3px;font-size:11px;color:#bbb;padding:8px 10px}
.submit{left:809px;top:2597px;width:153px;height:42px;background:#fff;color:#111;font-size:17px;border-radius:3px;display:flex;align-items:center;justify-content:center}
.bottom-bar{left:0;top:2681px;width:1200px;height:50px;background:var(--darker);color:#ccc;font-size:14px;display:flex;align-items:center;justify-content:center;gap:5px}
.bottom-bar b{color:var(--yellow);font-family:"Roboto Slab",Georgia,serif;font-weight:700;font-size:17px}
</style>
</head>
<body>

<div class="abs header"></div>
<div class="abs topline"></div>
<div class="abs brand">Marvenholt Leisure</div>
<div class="abs tagline">Health, Wellness, Fitness, Consultants</div>
<div class="abs callus">Call Us : <b>01632-960418</b></div>
<div class="abs account">
  <svg width="18" height="18" viewBox="0 0 18 18"><circle cx="9" cy="5.5" r="4" fill="var(--yellow)"/><path d="M1 18c0-5 3.5-7 8-7s8 2 8 7z" fill="var(--yellow)"/></svg>
  My Account
</div>
<div class="abs nav active" style="left:437px">Home</div>
<div class="abs nav" style="left:519px">About</div>
<div class="abs nav" style="left:605px">Health</div>
<div class="abs nav" style="left:697px">Fitness</div>
<div class="abs nav" style="left:790px">Brisk Forge</div>
<div class="abs nav" style="left:907px">Testimonial</div>
<div class="abs nav" style="left:1036px">Contact Us</div>

<div class="abs hero" role="img" aria-label="Dark gym interior with weight benches"></div>
<div class="abs hero-figures" role="img" aria-label="Two athletes posing together in the gym"></div>
<div class="abs hero-kicker">DISCOVER THE FITNESS WITH US!</div>
<div class="abs hero-title">TRY US TODAY!</div>
<div class="abs hero-text">We provide our best opportunity and qualified trainers for best workout yourself as you want!</div>
<div class="abs btn-light">Join us today!</div>

<div class="abs section-title" style="top:722px">Welcome to <span>MARVENHOLT LEISURE</span></div>
<div class="abs welcome-text">Marvenholt Leisure are leading consultants to the Health, Wellness and Fitness industry, with over 25 years experience working with some of the biggest global worldwide brands from equipment providers and facility operators to mass participation events and obstacle course races. Marvenholt Leisure is a multi disciplined business specialising in helping brands grow through insight, strategy creation and valuable sector collaboration, recent clients include the exclusive distribution of Brisk Forge bodyweight training products for the UK and Ireland, exclusive distribution of fitness app Tempo Tracks, Ridgeline Stride Race, Crest Volley, Pivot Cardio, Strata Motion UK, Brightvale Leisure, Active Fernmoor, Oldbridge Community Leisure, Trim Path Coach, VitaLoop and regional health trusts. The Marvenholt Leisure team specialise in a bespoke, consultative approach for each project.</div>

<div class="abs card card-health" role="img" aria-label="Group stretching outdoors in a park"><div class="card-label">Health</div></div>
<div class="abs card card-wellness" role="img" aria-label="Stacked pebbles by the sea"><div class="card-label">Wellness</div></div>
<div class="abs card card-fitness" role="img" aria-label="Athlete training in a dark gym">
  <div class="fitness-frame">
    <h3>Fitness</h3>
    <p>Lorem Ipsum is simply dummy text of the printing and typesetting industry. Lorem Ipsum has been the industry's standard dummy text ever since the</p>
  </div>
</div>

<div class="abs testimonial-band" role="img" aria-label="Faded dumbbells in the background"></div>
<div class="abs section-title" style="top:1300px">Testimonial</div>
<div class="abs quote">Ridgeline Stride Race and Marvenholt Leisure first collaborated in 2015. Owen and the Marvenholt team have showed impeccable drive, commitment, passion and integrity throughout our partnership. With the help of the Marvenholt team Stride Race have gained huge success in the UK in 2015 and we are in great shape for 2016. Their ability to go to market quickly, professionally, with tenacity and high energy enables me to personally recommend the Marvenholt Leisure organisation to anyone, or any company who requires a genuine, successful business collaboration and wants a great return on their investment "Highly Recommended"</div>
<div class="abs quote-rule"></div>
<div class="abs quote-name">- Colm Varrick</div>
<div class="abs quote-role">Stride Race CEO &amp; Founder of Stride Race</div>

<div class="abs section-title" style="top:1713px">Our <span>TEAM</span></div>

<svg class="abs arrow" style="left:28px" width="20" height="56" viewBox="0 0 20 56"><path d="M16 2 4 28l12 26" fill="none" stroke="#222" stroke-width="2"/></svg>
<svg class="abs arrow" style="left:1152px" width="20" height="56" viewBox="0 0 20 56"><path d="M4 2l12 26L4 54" fill="none" stroke="#222" stroke-width="2"/></svg>

<div class="abs member" style="left:78px">
  <div class="photo highlight" role="img" aria-label="Portrait of the owner">
    <div class="link-box"><svg width="24" height="24" viewBox="0 0 24 24" fill="none" stroke="#fff" stroke-width="2"><path d="M10 14l4-4"/><rect x="2" y="11" width="10" height="6" rx="3" transform="rotate(-45 7 14)"/><rect x="12" y="7" width="10" height="6" rx="3" transform="rotate(-45 17 10)"/></svg></div>
  </div>
  <div class="member-name dark">Marvenholt Leisure</div>
  <div class="member-role">Owner/Managing Director</div>
  <div class="member-rule"></div>
  <div class="socials"><svg width="20" height="14" viewBox="0 0 20 14"><rect x="0" y="0" width="20" height="14" fill="#999"/><path d="M0 0l10 8 10-8" fill="none" stroke="#fff" stroke-width="1.5"/></svg><div class="dot"></div><div class="dot"></div></div>
</div>
<div class="abs member" style="left:350px">
  <div class="photo" role="img" aria-label="Portrait of the managing director"></div>
  <div class="member-name">Dane Ashworth</div>
  <div class="member-role">Managing Director</div>
  <div class="member-rule"></div>
  <div class="socials"><svg width="20" height="14" viewBox="0 0 20 14"><rect width="20" height="14" fill="#bbb"/><path d="M0 0l10 8 10-8" fill="none" stroke="#fff" stroke-width="1.5"/></svg><div class="dot" style="background:#bbb"></div><div class="dot" style="background:#bbb"></div></div>
</div>
<div class="abs member" style="left:621px">
  <div class="photo" role="img" aria-label="Portrait of a trainer"></div>
  <div class="member-name">Reuben Talloway</div>
  <div class="member-role">Trainer</div>
  <div class="member-rule"></div>
  <div class="socials"><svg width="20" height="14" viewBox="0 0 20 14"><rect width="20" height="14" fill="#bbb"/><path d="M0 0l10 8 10-8" fill="none" stroke="#fff" stroke-width="1.5"/></svg><div class="dot" style="background:#bbb"></div><div class="dot" style="background:#bbb"></div></div>
</div>
<div class="abs member" style="left:890px">
  <div class="photo" role="img" aria-label="Portrait of a trainer"></div>
  <div class="member-name">Lewis Carnby</div>
  <div class="member-role">Trainer</div>
  <div class="member-rule"></div>
  <div class="socials"><svg width="20" height="14" viewBox="0 0 20 14"><rect width="20" height="14" fill="#bbb"/><path d="M0 0l10 8 10-8" fill="none" stroke="#fff" stroke-width="1.5"/></svg><div class="dot" style="background:#bbb"></div><div class="dot" style="background:#bbb"></div></div>
</div>

<div class="abs club"></div>
<div class="abs club-figures" role="img" aria-label="Two people lifting dumbbells"></div>
<div class="abs club-title">Join Our HEALTH CLUB</div>
<div class="abs club-sub">Lorem ipsum dolor sit amet, consectetur adipiscing elit, sed do.</div>
<div class="abs btn-dark">Request a quote</div>

<div class="abs footer"></div>
<div class="abs foot-head" style="left:80px">Our Blogs</div>
<div class="abs foot-head" style="left:350px">Contact</div>
<div class="abs foot-head" style="left:641px">Send a Message</div>

<div class="abs blog" style="top:2458px">
  <div class="avatar" role="img" aria-label="Blog thumbnail"></div>
  <div><div class="blog-title">Lorem Ipsum is simply dummy text of</div><div class="blog-meta">Today 5:60 pm - 12.06.2015</div></div>
</div>
<div class="abs blog" style="top:2544px">
  <div class="avatar" role="img" aria-label="Blog thumbnail"></div>
  <div><div class="blog-title">Lorem Ipsum is simply dummy text of</div><div class="blog-meta">Today 2:10 pm - 12.06.2015</div></div>
</div>

<div class="abs contact-item" style="top:2462px">
  <svg width="24" height="38" viewBox="0 0 24 38" fill="none" stroke="#999" stroke-width="2"><rect x="2" y="1" width="20" height="36" rx="3"/><line x1="2" y1="7" x2="22" y2="7"/><line x1="2" y1="30" x2="22" y2="30"/></svg>
  <div><div class="label">Call Now</div><div class="value">01632-960418</div></div>
</div>
<div class="abs contact-item" style="top:2524px">
  <svg width="28" height="20" viewBox="0 0 28 20" fill="none" stroke="#999" stroke-width="2"><rect x="1" y="1" width="26" height="18"/><path d="M1 1l13 10 13-10"/></svg>
  <div><div class="label">General question</div><div class="value">info@marvenholt.com</div></div>
</div>
<div class="abs contact-item" style="top:2584px">
  <svg width="24" height="32" viewBox="0 0 24 32"><path d="M12 1C6 1 2 5.5 2 11c0 8 10 20 10 20s10-12 10-20C22 5.5 18 1 12 1z" fill="#999"/><circle cx="12" cy="11" r="4" fill="var(--dark)"/></svg>
  <div><div class="value">123,Lorem ipsum text,<br>Country-123456.</div></div>
</div>

<div class="abs field" style="left:639px;top:2462px;width:239px;height:42px">Name *</div>
<div class="abs field" style="left:885px;top:2462px;width:237px;height:42px">Email Id *</div>
<div class="abs field" style="left:639px;top:2509px;width:483px;height:81px">Message *</div>
<div class="abs submit">SUBMIT</div>

<div class="abs bottom-bar">© 2017 <b>Marvenholt Leisure.</b> All rights reserved</div>

</body>
</html>
```